Valdane Companies Business Card Design

We need a new business card for our Private Equity Real Estate Development firm, “Valdane” and our EB-5 regional center “Thornmere Regional Center” on one card. We prefer a design that is simple, elegant, and represents the luxury products we design and build as well as the financial security and stability our successful history has produced. We are an industry leader in our field and 3rd generation family business that has evolved into an institutional quality investment platform. Considered design size is standard business card dimensions (3.5 x 2 inches with an additional 1/8 inch space for design elements or backgrounds that extend beyond the finished size of your piece.

Target Market(s)

• High net worth individuals
• Highly skilled technical workers and physicians in the US seeking investment-based immigration opportunities
• Sophisticated private equity investors
• Intermediary partners include domestic attorneys and investment brokers, as well as international agent networks
• US real estate developers

Industry/Entity Type

Finance

Contact Information for Business Card

(Providing placeholder info for personal information, please design for longer character spaces, longer names and addresses etc..)
• Logo for Valdane
• Logo for Thornmere Regional Center
• Full name: Marcus Valdane
• Job title: CEO
• Email address: mvaldane@valdanecompanies.com
• Cell phone number: +1.555.314.2287
• Office number +1.555.628.4410
• Office address: Larkfield Court 5, 4817 Vista Orilla, Brookhollow, CA.
• Website: www.valdanecompanies.com

Font styles to use
Serif
Sans Serif

Colors
ec1f27
ffffff
000000

Requirements
Must have
• • Logo for Valdane
• • Logo for Thornmere Regional Center
• - Use rounded corners
• (See .ai file included for logos)
Nice to have
• • Simple, elegant design
• • Aesthetically compatible with our website design (www.valdanecompanies.com)
• • Color palette including but not limited to white, black, and red (as per logos)
Should not have
• - Not too much red color
• - Do not stack both logos on top of each other

```html
<!DOCTYPE html>
<html lang="en">
<head>
<meta charset="utf-8">
<title>Valdane Companies Business Card</title>
<link rel="stylesheet" href="https://fonts.googleapis.com/css2?family=Cinzel:wght@700&family=Lato:wght@400&display=swap">
<style>
  :root {
    --stage: #4a4a4a;
    --card: #2f2f2f;
    --ink: #ffffff;
    --ink-soft: #d9d9d9;
    --mark: #c9c9c9;
    --rule: #8a8a8a;
  }
  * { margin: 0; padding: 0; box-sizing: border-box; }
  html, body { width: 1200px; height: 912px; overflow: hidden; }
  body {
    background: var(--stage);
    position: relative;
    font-family: "Lato", Arial, sans-serif;
    color: var(--ink);
  }
  .card {
    position: absolute;
    width: 700px;
    height: 400px;
    background: var(--card);
    border-radius: 14px;
    box-shadow: 0 10px 28px rgba(0,0,0,0.35);
  }
  .card--front { left: 110px; top: 40px; }
  .card--back { left: 390px; top: 472px; }

  .brand {
    position: absolute;
    display: flex;
    align-items: center;
    gap: 16px;
  }
  .brand__square {
    width: 44px; height: 44px;
    background: var(--mark);
    flex: none;
  }
  .brand__name {
    font-family: "Cinzel", Georgia, serif;
    font-weight: 700;
    color: var(--ink);
    letter-spacing: 1px;
    white-space: nowrap;
  }
  .card--front .brand {
    left: 0; right: 0; top: 178px;
    justify-content: center;
  }
  .card--front .brand__name { font-size: 26px; }

  .card--back .brand {
    left: 20px; top: 168px;
    flex-direction: column;
    gap: 14px;
    width: 270px;
  }
  .card--back .brand__name { font-size: 21px; text-align: center; }

  .divider {
    position: absolute;
    left: 300px; top: 70px;
    width: 1px; height: 260px;
    background: linear-gradient(var(--card), var(--rule) 30%, var(--rule) 70%, var(--card));
  }
  .contact { position: absolute; left: 330px; top: 70px; }
  .contact__name {
    font-family: "Cinzel", Georgia, serif;
    font-weight: 700;
    font-size: 28px;
    letter-spacing: 1px;
    white-space: nowrap;
  }
  .contact__title { font-size: 20px; margin: 4px 0 0 24px; }
  .contact__address { font-size: 16px; line-height: 1.5; margin: 16px 0 0 50px; color: var(--ink-soft); white-space: nowrap; }
  .contact__list { list-style: none; margin: 20px 0 0 50px; font-size: 16px; line-height: 1.6; color: var(--ink-soft); }
  .contact__list li { display: flex; align-items: center; gap: 12px; white-space: nowrap; }
  .contact__list svg { width: 14px; height: 14px; fill: none; stroke: var(--ink); stroke-width: 1.6; flex: none; }
</style>
</head>
<body>
  <section class="card card--front" aria-label="Card front">
    <div class="brand">
      <span class="brand__square"></span>
      <span class="brand__name">THORNMERE REGIONAL CENTER</span>
    </div>
  </section>

  <section class="card card--back" aria-label="Card back">
    <div class="brand">
      <span class="brand__square"></span>
      <span class="brand__name">VALDANE CAPITAL</span>
    </div>
    <div class="divider"></div>
    <div class="contact">
      <h1 class="contact__name">MARCUS VALDANE</h1>
      <p class="contact__title">CEO</p>
      <p class="contact__address">Larkfield Court 5, 4817 Vista Orilla<br>Brookhollow, CA.</p>
      <ul class="contact__list">
        <li><svg viewBox="0 0 14 14"><path d="M3 1l2 3-1.5 1.5a7 7 0 0 0 5 5L10 9l3 2-1.5 2.5C6 13 1 8 .5 2.5z"/></svg>+1.555.314.2287</li>
        <li><svg viewBox="0 0 14 14"><rect x="3.5" y="1" width="7" height="12" rx="1"/></svg>+1.555.628.4410</li>
        <li><svg viewBox="0 0 14 14"><rect x="1" y="3" width="12" height="8"/><path d="M1 3l6 5 6-5"/></svg>mvaldane@valdanecompanies.com</li>
        <li><svg viewBox="0 0 14 14"><circle cx="7" cy="7" r="6"/><path d="M1 7h12M7 1c3 3 3 9 0 12M7 1c-3 3-3 9 0 12"/></svg>www.valdanecompanies.com</li>
      </ul>
    </div>
  </section>
</body>
</html>
```